Irrigation Business needs their business cards modernised and revamped

I would like to keep my current logo, colours and revamp the format of the card.

I would like the card to be clean yet important.

Im not sure if you include texture but i would like the named logo to be indented into the card etc.

show me something alive and free something thats clinical to the point yet has a feel of achievement. i would like people to go nice card.

Target Market(s)

high end clients, corporate, sports field manger, the guys that make the decisions

Industry/Entity Type

Business

Contact Information for Business Card

nformation to be included

Dean Harlow (Director)
0487305526
dean@kolvat.biz
www.kestonfieldworks.com

instagram logo
google logo
facebook logo

Colors

Designer to choose colors to be used in the design.

Requirements
Nice to have
• indentations a really nice feel to the card good texture

```html
<!DOCTYPE html>
<html lang="en">
<head>
<meta charset="utf-8">
<title>Keston Fieldworks — Business Card</title>
<link rel="stylesheet" href="https://fonts.googleapis.com/css2?family=Open+Sans:wght@400;600;700&display=swap">
<style>
  :root {
    --backdrop: #3b302a;
    --card: #28282b;
    --card-deep: #1e1e21;
    --brand-blue: #2f8fd6;
    --text-light: #e6e6e8;
    --text-muted: #a8a8ae;
    --emboss-hi: #47474c;
    --emboss-lo: #19191b;
  }
  * { box-sizing: border-box; margin: 0; padding: 0; }
  html, body { width: 1200px; height: 715px; overflow: hidden; }
  body {
    background: var(--backdrop);
    font-family: "Open Sans", Arial, sans-serif;
    position: relative;
  }
  .card {
    position: absolute;
    top: 200px;
    width: 540px;
    height: 310px;
    background: linear-gradient(160deg, var(--card) 0%, var(--card-deep) 100%);
    border-radius: 4px;
    overflow: hidden;
    box-shadow: 0 18px 40px rgba(0,0,0,.45);
  }
  .card-front { left: 40px; }
  .card-back { left: 620px; }

  .embossed-disc {
    position: absolute;
    top: 40px;
    width: 300px;
    height: 300px;
    border-radius: 50%;
    background: radial-gradient(circle at 40% 35%, var(--emboss-hi) 0%, #2c2c30 55%, var(--emboss-lo) 100%);
    box-shadow: inset 4px 4px 8px rgba(0,0,0,.7), inset -3px -3px 6px rgba(255,255,255,.08);
  }
  .card-front .embossed-disc { left: 390px; }
  .card-back .embossed-disc { left: -150px; }

  .brand {
    display: flex;
    align-items: center;
    gap: 10px;
    color: var(--brand-blue);
    font-weight: 700;
    letter-spacing: .04em;
    text-transform: uppercase;
  }
  .brand-dot {
    border-radius: 50%;
    background: var(--brand-blue);
    flex: none;
  }
  .card-front .brand { position: absolute; left: 34px; top: 34px; font-size: 17px; }
  .card-front .brand-dot { width: 30px; height: 30px; }
  .card-back .brand { position: absolute; right: 36px; bottom: 40px; font-size: 22px; }
  .card-back .brand-dot { width: 40px; height: 40px; }

  .holder { position: absolute; left: 34px; top: 100px; }
  .holder-name { color: var(--brand-blue); font-size: 18px; font-weight: 600; }
  .holder-role { color: var(--text-light); font-size: 12px; margin-top: 2px; }
  .holder-rule { width: 16px; height: 2px; background: var(--brand-blue); margin-top: 8px; }

  .contact-list { position: absolute; left: 34px; top: 176px; list-style: none; }
  .contact-list li {
    display: flex; align-items: center; gap: 10px;
    font-size: 12px; color: var(--text-light); margin-bottom: 8px;
  }
  .contact-list li.web { color: var(--brand-blue); }
  .contact-list svg { width: 12px; height: 12px; fill: none; stroke: var(--text-muted); stroke-width: 1.6; }

  .social-row { position: absolute; left: 262px; top: 262px; display: flex; gap: 6px; }
  .social-row span { width: 12px; height: 12px; border-radius: 50%; background: var(--brand-blue); }
</style>
</head>
<body>
  <section class="card card-front">
    <div class="embossed-disc" role="img" aria-label="Pressed circular emblem"></div>
    <div class="brand"><span class="brand-dot"></span>Keston Fieldworks</div>
    <div class="holder">
      <p class="holder-name">Dean Harlow</p>
      <p class="holder-role">Director</p>
      <div class="holder-rule"></div>
    </div>
    <ul class="contact-list">
      <li><svg viewBox="0 0 12 12"><path d="M3 1l2 2-1 1.5a6 6 0 003.5 3.5L9 7l2 2-1.5 2A9 9 0 011 2.5z"/></svg>0487305526</li>
      <li><svg viewBox="0 0 12 12"><rect x="1" y="2.5" width="10" height="7"/><path d="M1 3l5 4 5-4"/></svg>dean@kolvat.biz</li>
      <li class="web"><svg viewBox="0 0 12 12"><circle cx="6" cy="6" r="5"/><path d="M1 6h10M6 1c2.5 3 2.5 7 0 10M6 1c-2.5 3-2.5 7 0 10"/></svg>www.kestonfieldworks.com</li>
    </ul>
    <div class="social-row" aria-label="Social profiles"><span></span><span></span><span></span></div>
  </section>

  <section class="card card-back">
    <div class="embossed-disc" role="img" aria-label="Pressed circular emblem"></div>
    <div class="brand"><span class="brand-dot"></span>Keston Fieldworks</div>
  </section>
</body>
</html>
```